Tessaline Wellness Marketing Flyer

We are a new medical practice in the community and need a flyer to send to other medical offices to inform of our services. We just completed our logo with Draftmarketo and would like to incorporate that plus our marketing content into the flyer. Our medical practice has 2 divisions: (1)Mental Health/Psychiatry and (2) Migraine and Neurospasticity Management. Please see website for content and provider photos at www.TessaWellnet.com

Target Market(s)

Other Healthcare Professionals in the Community

Industry/Entity Type

Medical

Requirements
Must have
• Photos of all 5 healthcare providers, phone number, address, logo

```html
<!DOCTYPE html>
<html lang="en">
<head>
<meta charset="UTF-8">
<title>Tessaline Wellness Flyer</title>
<link href="https://fonts.googleapis.com/css2?family=Oswald:wght@600;700&family=Montserrat:wght@400;500;600;700;800&display=swap" rel="stylesheet">
<style>
:root{
  --navy:#1d2a45;
  --green:#8cc63f;
  --green-dark:#6aa329;
  --teal:#178a86;
  --card:#eef1f0;
  --text:#39424f;
  --page:#d9dcdc;
  --white:#ffffff;
}
*{margin:0;padding:0;box-sizing:border-box}
html,body{width:1200px;height:2400px;overflow:hidden;background:var(--page);font-family:'Montserrat',sans-serif;color:var(--text)}
.flyer{position:absolute;left:30px;top:30px;width:1140px;height:2340px;background:var(--white);overflow:hidden}
.hero-art{position:absolute;right:0;top:0;width:620px;height:660px}
.brand{position:absolute;left:60px;top:60px;display:flex;align-items:center;gap:14px}
.brand-dot{width:40px;height:40px;border-radius:50%;background:var(--green)}
.brand-name{font-size:32px;font-weight:700;color:var(--navy);letter-spacing:1px}
.headline{position:absolute;left:60px;top:220px;font-family:'Oswald',sans-serif;font-weight:700;font-size:98px;line-height:1.02;color:var(--navy);text-transform:uppercase}
.subtitle{position:absolute;left:60px;top:570px;width:640px;font-size:38px;font-weight:700;color:var(--teal);line-height:1.22}
.section-title{font-size:38px;font-weight:800;color:var(--green-dark)}
.mental{position:absolute;left:60px;top:740px;width:560px}
.mental p{margin-top:14px;font-size:19px;line-height:1.5}
.providers{position:absolute;left:60px;top:1020px;width:560px;display:grid;grid-template-columns:1fr 1fr;gap:70px 20px}
.provider{background:var(--card);border-radius:14px;padding:96px 20px 24px;position:relative;height:470px;border-top:6px solid var(--green)}
.provider-photo{position:absolute;left:50%;top:-70px;width:140px;height:140px;margin-left:-70px;border-radius:50%;background:linear-gradient(135deg,#b9a89a,#6f7d86);border:5px solid var(--white)}
.provider-name{font-size:24px;font-weight:700;color:var(--navy);text-align:center}
.provider-title{font-size:15px;font-weight:600;color:var(--teal);text-align:center;margin:4px 0 14px}
.provider-bio{font-size:16px;line-height:1.5;text-align:center}
.migraine{position:absolute;left:660px;top:740px;width:420px}
.doctor{display:flex;align-items:center;gap:18px}
.doctor-photo{flex:none;width:150px;height:150px;border-radius:50%;background:linear-gradient(135deg,#c2b3a5,#5f6f7b);border:5px solid var(--green)}
.doctor-name{font-size:20px;font-weight:600;color:var(--teal)}
.doctor-area{font-size:26px;font-weight:800;color:var(--navy);line-height:1.2;margin-top:4px}
.migraine p{margin-top:22px;font-size:18px;line-height:1.5}
.services{position:absolute;left:660px;top:1330px;width:420px}
.services::before{content:"";position:absolute;left:14px;top:20px;bottom:60px;width:4px;background:var(--green)}
.service{position:relative;margin-left:48px;margin-bottom:34px;background:var(--green);color:var(--white);border-radius:14px;padding:26px 26px}
.service::before{content:"";position:absolute;left:-48px;top:22px;width:32px;height:32px;border-radius:50%;background:var(--navy);border:5px solid var(--white)}
.service h3{font-size:26px;font-weight:800;line-height:1.2;color:var(--navy)}
.service p{margin-top:10px;font-size:17px;line-height:1.5}
.footer{position:absolute;left:0;bottom:0;width:1140px;height:300px}
.footer-bg{position:absolute;inset:0}
.footer-items{position:absolute;left:60px;right:60px;bottom:60px;display:flex;align-items:center;justify-content:space-between;color:var(--white)}
.contact{display:flex;align-items:center;gap:14px;font-size:19px;line-height:1.4}
.contact svg{flex:none}
.phone{font-size:36px;font-weight:800;color:var(--green)}
.web{font-size:24px;font-weight:700;color:var(--green)}
</style>
</head>
<body>
<div class="flyer">
  <svg class="hero-art" viewBox="0 0 620 660">
    <circle cx="380" cy="290" r="330" fill="var(--green)"/>
    <circle cx="390" cy="280" r="300" fill="var(--white)"/>
    <path d="M120 620 Q360 700 620 560 L620 660 L80 660 Z" fill="var(--green)" opacity="0.35"/>
    <circle cx="400" cy="270" r="285" fill="url(#heroFill)" role="img" aria-label="Photo of a smiling woman holding a phone outdoors"/>
    <defs>
      <linearGradient id="heroFill" x1="0" y1="0" x2="1" y2="1">
        <stop offset="0" stop-color="#d9d3cc"/>
        <stop offset="0.5" stop-color="#a99483"/>
        <stop offset="1" stop-color="#6c6e72"/>
      </linearGradient>
    </defs>
  </svg>

  <div class="brand"><span class="brand-dot"></span><span class="brand-name">Tessaline Wellness</span></div>

  <h1 class="headline">Helping Bodies<br>Helping Minds<br>Helping You..</h1>
  <h2 class="subtitle">Mental Health and Psychiatry Services Migraine and Neurospasticity Intervention</h2>

  <section class="mental">
    <h2 class="section-title">Mental Health/Psychiatry</h2>
    <p>Bringing comprehensive evaluation, medication management and psychotherapy to the full spectrum of mental health disorders including minor, moderate and major depression, bipolar disorder, ADD/ADHD, anxiety, schizophrenia, stress or grief reactions, and others.</p>
  </section>

  <div class="providers">
    <article class="provider">
      <div class="provider-photo" role="img" aria-label="Portrait of provider Marcus Tolliver"></div>
      <h3 class="provider-name">Marcus Tolliver</h3>
      <div class="provider-title">PMHNP - BC</div>
      <p class="provider-bio">Before entering psychiatry, he spent years in acute care nursing and now brings calm, thorough evaluation and steady medication management to adults and teens seeking relief.</p>
    </article>
    <article class="provider">
      <div class="provider-photo" role="img" aria-label="Portrait of provider Dorian Whitfield"></div>
      <h3 class="provider-name">Dorian Whitfield</h3>
      <div class="provider-title">PMHNP - BC</div>
      <p class="provider-bio">With a strong background in community behavioral health, he partners with each patient to build practical treatment plans for depression, anxiety and mood disorders.</p>
    </article>
    <article class="provider">
      <div class="provider-photo" role="img" aria-label="Portrait of provider Emmett Crane"></div>
      <h3 class="provider-name">Emmett Crane</h3>
      <div class="provider-title">PMHNP - BC</div>
      <p class="provider-bio">Focused on whole-person care, he treats ADHD, bipolar disorder and trauma-related conditions, combining careful listening with evidence-based medication options for lasting results.</p>
    </article>
    <article class="provider">
      <div class="provider-photo" role="img" aria-label="Portrait of provider Lydia Ferrow"></div>
      <h3 class="provider-name">Lydia Ferrow</h3>
      <div class="provider-title">PMHNP - BC</div>
      <p class="provider-bio">She brings over a decade of psychiatric nursing experience and a gentle, direct style to helping patients and families navigate complex mental health needs.</p>
    </article>
  </div>

  <section class="migraine">
    <div class="doctor">
      <div class="doctor-photo" role="img" aria-label="Portrait of Dr. Corwin Adler"></div>
      <div>
        <div class="doctor-name">Dr. Corwin Adler</div>
        <div class="doctor-area">Migraine and Neurospasticity Management</div>
      </div>
    </div>
    <p>Injections of botulinum neurotoxin are a widely used therapeutic form of treatment for both chronic migraines and patients with Parkinson's, muscle contractures ("neurospasticity"). Injections may offer up to 4 months of relief and may be combined with other pharmaceutical interventions for maximum benefit.</p>
  </section>

  <div class="services">
    <div class="service">
      <h3>New Patient Evaluation</h3>
      <p>Thorough consultation to review history and determine the best approach for migraine or spasticity concerns.</p>
    </div>
    <div class="service">
      <h3>Insurance Pre-Authorization</h3>
      <p>Our team handles insurance pre-authorization so treatment can begin promptly, without extra work for your office.</p>
    </div>
    <div class="service">
      <h3>Follow-Up Appointments</h3>
      <p>Regular follow-up visits track progress and adjust treatment to keep patients comfortable and well.</p>
    </div>
  </div>

  <footer class="footer">
    <svg class="footer-bg" viewBox="0 0 1140 300" preserveAspectRatio="none">
      <path d="M0 60 Q570 0 1140 70 L1140 300 L0 300 Z" fill="var(--green)"/>
      <path d="M0 90 Q570 30 1140 100 L1140 300 L0 300 Z" fill="var(--navy)"/>
    </svg>
    <div class="footer-items">
      <div class="contact">
        <svg width="34" height="44" viewBox="0 0 24 32"><path d="M12 0C5.4 0 0 5.2 0 11.7 0 20.5 12 32 12 32s12-11.5 12-20.3C24 5.2 18.6 0 12 0zm0 16.5a5 5 0 110-10 5 5 0 010 10z" fill="var(--green)"/></svg>
        <span>Tessaline Wellness 2150 W. Larkspur Ave,<br>Suite B, Meridian, ID 83642</span>
      </div>
      <div class="contact">
        <svg width="38" height="38" viewBox="0 0 24 24"><path d="M6.6 10.8a15.2 15.2 0 006.6 6.6l2.2-2.2a1 1 0 011-.25 11.4 11.4 0 003.6.57 1 1 0 011 1V20a1 1 0 01-1 1A17 17 0 013 4a1 1 0 011-1h3.5a1 1 0 011 1c0 1.25.2 2.45.57 3.57a1 1 0 01-.25 1z" fill="var(--green)"/></svg>
        <span class="phone">(208) 555-0142</span>
      </div>
      <div class="contact">
        <svg width="34" height="34" viewBox="0 0 24 24" fill="none" stroke="var(--green)" stroke-width="2"><circle cx="12" cy="12" r="10"/><path d="M2 12h20M12 2c3 3.5 3 16.5 0 20M12 2c-3 3.5-3 16.5 0 20"/></svg>
        <span class="web">www.TessaWellnet.com</span>
      </div>
    </div>
  </footer>
</div>
</body>
</html>
```